SkyvornQ Business Cards and Stationary Design

Need a design for our business cards and stationary. I want to carry on the theme of the logo. I want the business cards to have a design on the back. I would like the business cards and the stationary to carry the same theme, design scheme, and branding

Target Market(s)

Airlines and Maintenance Facilities

Industry/Entity Type

Aviation

Contact Information for Business Card

Name
Position Title
Address: 4827 Trellis Hollow Road, Brenmoor Falls, Ohio, 43218
Office Number
Mobile Number
Email
Website

Font styles to use
Serif
Sans Serif

Colors

Designer to choose colors to be used in the design.

```html
<!DOCTYPE html>
<html lang="en">
<head>
<meta charset="utf-8">
<title>SkyvornQ Business Cards</title>
<link href="https://fonts.googleapis.com/css2?family=Michroma&family=Open+Sans:wght@400&display=swap" rel="stylesheet">
<style>
  :root {
    --backdrop: #e7e4e1;
    --card: #ffffff;
    --navy: #0b3068;
    --sky: #2a8fdc;
    --ink-light: #ffffff;
  }
  html, body {
    margin: 0;
    padding: 0;
    width: 1200px;
    height: 997px;
    overflow: hidden;
    background: var(--backdrop);
  }
  .canvas {
    position: relative;
    width: 1200px;
    height: 997px;
  }
  .card {
    position: absolute;
    width: 520px;
    height: 300px;
    background: var(--card);
    box-shadow: 0 6px 18px rgba(0, 0, 0, 0.12);
    overflow: hidden;
  }
  .card--front { left: 100px; top: 170px; }
  .card--back { left: 580px; top: 480px; }
  .card__shapes {
    position: absolute;
    inset: 0;
  }
  .brand-name {
    font-family: "Michroma", sans-serif;
    color: var(--navy);
    letter-spacing: 3px;
    margin: 0;
    line-height: 1;
  }
  .card--front .brand-name {
    position: absolute;
    left: 36px;
    top: 96px;
    font-size: 24px;
  }
  .contact-list {
    position: absolute;
    left: 36px;
    top: 196px;
    margin: 0;
    padding: 0;
    list-style: none;
    font-family: "Open Sans", sans-serif;
    font-size: 12.5px;
    color: var(--ink-light);
  }
  .contact-list li {
    display: flex;
    align-items: center;
    gap: 10px;
    height: 22px;
  }
  .contact-list svg {
    width: 12px;
    height: 12px;
    flex: none;
  }
  .card--back .brand-name {
    position: absolute;
    left: 0;
    right: 0;
    top: 146px;
    text-align: center;
    font-size: 30px;
  }
  .web-line {
    position: absolute;
    left: 80px;
    right: 80px;
    top: 204px;
    display: flex;
    align-items: center;
    gap: 12px;
    font-family: "Open Sans", sans-serif;
    font-size: 13px;
    letter-spacing: 2px;
    color: var(--navy);
  }
  .web-line::before,
  .web-line::after {
    content: "";
    flex: 1;
    height: 1px;
    background: var(--navy);
  }
</style>
</head>
<body>
<main class="canvas">

  <section class="card card--front" aria-label="Business card front">
    <svg class="card__shapes" width="520" height="300" viewBox="0 0 520 300">
      <polygon points="0,172 520,92 520,300 0,300" fill="#0b3068"/>
      <line x1="0" y1="169" x2="520" y2="89" stroke="#2a8fdc" stroke-width="2"/>
      <circle cx="452" cy="78" r="56" fill="#ffffff" stroke="#0b3068" stroke-width="6"/>
      <circle cx="78" cy="58" r="20" fill="#2a8fdc"/>
    </svg>
    <p class="brand-name">SKYVORNQ</p>
    <ul class="contact-list">
      <li>
        <svg viewBox="0 0 12 12"><path d="M2 1h3l1 3-2 1a7 7 0 0 0 3 3l1-2 3 1v3c-6 0-10-4-10-10z" fill="#fff"/></svg>
        001 555 0148
      </li>
      <li>
        <svg viewBox="0 0 12 12"><rect x="3" y="0.5" width="6" height="11" rx="1" fill="none" stroke="#fff"/></svg>
        001 555 0148
      </li>
      <li>
        <svg viewBox="0 0 12 12"><rect x="0.5" y="2.5" width="11" height="7" fill="none" stroke="#fff"/><path d="M0.5 2.5l5.5 4 5.5-4" fill="none" stroke="#fff"/></svg>
        info@skyvornq.com
      </li>
      <li>
        <svg viewBox="0 0 12 12"><path d="M6 0.5a4 4 0 0 1 4 4c0 3-4 7-4 7s-4-4-4-7a4 4 0 0 1 4-4z" fill="#fff"/><circle cx="6" cy="4.5" r="1.5" fill="#0b3068"/></svg>
        4827 Trellis Hollow Road, Brenmoor Falls, Ohio, 43218
      </li>
    </ul>
  </section>

  <section class="card card--back" aria-label="Business card back">
    <svg class="card__shapes" width="520" height="300" viewBox="0 0 520 300">
      <circle cx="260" cy="96" r="30" fill="#2a8fdc"/>
    </svg>
    <p class="brand-name">SKYVORNQ</p>
    <div class="web-line">www.skyvornq.com</div>
  </section>

</main>
</body>
</html>
```